New design for www.TrimTable.com

On TrimTable you can find & book your hairdresser. TrimTable is the biggest platform in the Netherlands.

- The design should be a responcive design
- Should be able to go global, should fit in perfectly between all the big booking platforms like stayvo, ridlo etc,
- Should have te result of more bookings. :)
- We are ‘only’ asking a beautiful design, not a technical solution.
- We need a homepage (https://trimtable.com/), search resultpage ((https://trimtable.com/kapper/amsterdam/#), salonpage (https://trimtable.com/kapper/vorden/lumo-for-hair/), about us page (https://trimtable.com/aboutus/), for the hairdresser info page (https://trimtable.com/kapper/), login/register page (https://trimtable.com/account/signin/).

- On the page of the hairdresser there is a dynamic part. The part where you create your appointment. Please take a look at this part too after you choose your treatment (behandeling), employee (medewerker), Date (datum) and time (tijd). The part that you see after this, is the part where you fill in your data as a consumer.

I've added more logo's but mostly we use the green color.

A few of our competitors: www.plumsalo.com, www.korifex.com

Target Market(s)

All consumers

Industry/Entity Type

Hair And Beauty

Number of Pages Required

5+ page

Font styles to use
Sans Serif

Colors
abd036
c3c3c3
757575

Requirements
Must have
• Responsive
• We did an A/B test with the homepage. It turns out that option B works better then option A (take a look at the uploaded pictures). So what we need on the homepage: The USP's with the green checkboxes, The search button needs to by dynamic (changes for example from light green to dark green so you can see you can click it) The call to action sentence Zoek & Vind je kapsalon, the searchfield and searchbutton should be seperated.
Nice to have
• The style that we like is the flat design style. The website should be simple, clean and it should feel a bit like a luxury thing. Because an appointment with the hairdresser can be a real treat and luxury moment for yourself.
• The luxury feeling and flat design that is in the www.ridlo.com website is really nice for example. But then it has to be a bit more light and not so black and dark.

```html
<!DOCTYPE html>
<html lang="en">
<head>
<meta charset="utf-8">
<title>TrimTable – Find &amp; book your hairdresser</title>
<link href="https://fonts.googleapis.com/css2?family=Oswald:wght@400;500;600&family=Open+Sans:ital,wght@0,400;0,600;0,700;1,400&display=swap" rel="stylesheet">
<style>
:root{
  --green:#abd036;
  --green-dark:#86a923;
  --green-deep:#6b8a17;
  --ink:#2b2b2b;
  --dark:#1c1c1c;
  --grey:#757575;
  --grey-light:#c3c3c3;
  --paper:#f1f1f1;
  --white:#ffffff;
}
*{box-sizing:border-box;margin:0;padding:0}
html,body{width:1200px;height:4444px;overflow:hidden}
body{font-family:"Open Sans",Arial,sans-serif;color:var(--ink);background:var(--white);font-size:13px;line-height:1.6}
h1,h2,h3,h4{font-family:"Oswald","Arial Narrow",sans-serif;font-weight:500;text-transform:uppercase;letter-spacing:.5px}
.icon-defs{position:absolute;width:0;height:0}
.btn{display:inline-block;font-family:"Oswald",sans-serif;text-transform:uppercase;font-size:14px;letter-spacing:.5px;padding:10px 22px;border-radius:3px;color:var(--white);cursor:pointer;transition:background .2s}
.btn-green{background:var(--green)}
.btn-green:hover{background:var(--green-deep)}
.btn-outline{border:2px solid var(--white)}

/* HERO */
.hero{position:relative;height:640px;background:#2a2523;overflow:hidden}
.hero-photo{position:absolute;right:0;top:0;width:780px;height:640px;background:radial-gradient(ellipse at 55% 45%,#b58b77 0%,#7a5446 30%,#3b2a25 62%,#2a2523 100%)}
.hero-shade{position:absolute;inset:0;background:linear-gradient(90deg,rgba(30,26,25,.9) 0%,rgba(30,26,25,.55) 40%,rgba(30,26,25,0) 70%)}
.topbar{position:absolute;top:0;left:0;right:0;height:80px;display:flex;align-items:center;justify-content:space-between;padding:0 80px;z-index:2}
.brand{display:flex;align-items:center;gap:10px;font-weight:700;font-size:24px;color:var(--white)}
.brand-dot{width:28px;height:28px;border-radius:50%;background:var(--green)}
.nav{display:flex;align-items:center;gap:26px;font-family:"Oswald",sans-serif;text-transform:uppercase;font-size:14px;color:var(--white)}
.nav .btn{padding:6px 14px;font-size:13px}
.hero-copy{position:absolute;left:80px;top:210px;z-index:2;color:var(--white);width:520px}
.hero-copy h1{font-size:44px;line-height:1.15;font-weight:600}
.hero-tag{font-family:"Oswald",sans-serif;text-transform:uppercase;font-size:16px;margin-top:10px}
.hero-lede{font-size:12px;color:#cfcfcf;margin-top:6px;line-height:1.5}
.usp-list{list-style:none;margin-top:18px;display:flex;flex-direction:column;gap:8px}
.usp-list li{display:flex;align-items:center;gap:10px;font-size:13px;font-weight:600}
.usp-check{width:20px;height:20px;border-radius:50%;background:var(--green);display:flex;align-items:center;justify-content:center;flex:none}
.hero-actions{margin-top:24px;display:flex;gap:18px}

/* SEARCH BAR */
.search{height:120px;background:var(--green);display:flex;align-items:center;padding-right:80px}
.search-title{height:120px;width:300px;background:var(--green-dark);display:flex;align-items:center;padding-left:80px;position:relative;color:var(--white);font-size:24px;line-height:1.1;font-family:"Oswald",sans-serif;text-transform:uppercase;font-weight:500}
.search-title::after{content:"";position:absolute;right:-30px;top:0;border-left:30px solid var(--green-dark);border-top:60px solid transparent;border-bottom:60px solid transparent}
.search-form{display:flex;align-items:center;gap:24px;margin-left:60px;flex:1}
.field{display:flex;align-items:center;gap:8px}
.field-icon{width:36px;height:36px;border-radius:50%;border:2px solid var(--white);display:flex;align-items:center;justify-content:center;flex:none}
.field-input{width:250px;height:40px;background:var(--white);border-radius:2px;color:var(--grey);font-size:13px;padding:10px 12px}
.search-btn{margin-left:auto;background:var(--green-deep);padding:10px 30px;display:flex;align-items:center;gap:10px}
.search-btn:hover{background:var(--dark)}

/* SECTION HEADINGS */
.section-title{display:flex;align-items:center;justify-content:center;gap:22px;color:var(--ink)}
.section-title .rule{width:150px;height:1px;background:var(--grey-light)}
.section-title h2{font-size:30px;line-height:1.1;text-align:center}
.section-title h2 span{display:block;color:var(--green-dark)}
.scissors{width:34px;height:34px;color:var(--ink)}

/* SERVICES */
.services{height:440px;background:var(--paper);padding-top:60px}
.services-title h2{border:2px solid var(--ink);padding:6px 18px;font-size:26px}
.service-list{display:flex;justify-content:space-between;padding:0 110px;margin-top:60px}
.service{width:170px;text-align:center}
.service-icon{width:72px;height:72px;border-radius:50%;background:var(--white);margin:0 auto 16px;display:flex;align-items:center;justify-content:center;box-shadow:0 0 0 1px #ddd}
.service h3{font-size:14px;margin-bottom:6px}
.service p{font-size:11px;color:var(--grey);line-height:1.5}

/* WELCOME */
.welcome{height:420px;display:flex;padding:40px 80px;gap:50px}
.welcome-photo{width:440px;height:340px;border-radius:6px;background:linear-gradient(135deg,#8a4a2e 0%,#c58b63 45%,#e2c7a9 75%,#a86c4a 100%)}
.welcome-copy{flex:1;padding-top:10px}
.welcome-head{display:flex;align-items:center;gap:14px}
.pin-badge{width:40px;height:48px}
.welcome-head h2{font-size:30px;line-height:1.05}
.welcome-head h2 span{color:var(--green-dark);display:block}
.welcome-head .rule{flex:1;height:1px;background:var(--grey-light)}
.welcome-copy p{font-size:11.5px;color:var(--grey);margin-top:14px;line-height:1.7}
.welcome-copy .btn{margin-top:22px;padding:8px 18px}

/* STATS */
.stats{height:380px;background:radial-gradient(ellipse at 50% 40%,#3a3a3a 0%,#1f1f1f 55%,#111 100%);display:flex;justify-content:space-between;padding:60px 120px 0}
.stat{width:160px;text-align:center;color:var(--white)}
.stat-ring{width:120px;height:150px;margin:0 auto;display:block}
.stat h3{font-size:15px;font-weight:400;margin-top:20px;line-height:1.3}

/* APP */
.app{height:420px;display:flex;align-items:center;padding:0 80px}
.app-copy{width:640px}
.app-copy h2{font-family:"Open Sans",sans-serif;text-transform:none;font-weight:700;font-size:24px;letter-spacing:0;white-space:nowrap}
.app-copy p{font-style:italic;color:var(--grey);font-size:13px;margin-top:14px;line-height:1.7}
.app-copy .btn{margin-top:26px}
.app-device{margin-left:auto;width:380px;height:340px;border-radius:30px;background:linear-gradient(150deg,#f5f5f5 0%,#d9d9d9 40%,#d7e58f 60%,#abd036 100%)}

/* HOW IT WORKS */
.how{height:500px;background:#f3f3f3;padding-top:60px}
.how-steps{position:relative;height:300px;margin-top:40px}
.how-path{position:absolute;left:0;top:0;width:1200px;height:300px}
.step{position:absolute;top:50px;width:260px;text-align:center}
.step-icon{width:104px;height:104px;border-radius:50%;border:2px solid var(--green);background:var(--white);margin:0 auto 20px;display:flex;align-items:center;justify-content:center}
.step h3{font-size:15px;line-height:1.35}

/* PORTFOLIO */
.portfolio{height:620px;padding-top:60px}
.portfolio-intro{text-align:center;width:900px;margin:18px auto 0;font-size:11.5px;color:var(--grey);line-height:1.7}
.gallery{display:flex;margin:50px 80px 0;height:360px}
.gallery-lead{width:250px;background:var(--green);color:var(--white);padding:34px 26px;position:relative}
.gallery-lead h3{font-size:22px}
.gallery-lead p{font-size:11px;margin-top:10px;line-height:1.6}
.gallery-arrows{position:absolute;left:26px;bottom:40px;display:flex;gap:6px}
.gallery-arrows span{width:26px;height:26px;background:var(--dark);display:flex;align-items:center;justify-content:center}
.gallery-photo{flex:1}
.gallery-photo.g1{background:linear-gradient(160deg,#4a3a2e,#b98a5f,#6b4a33)}
.gallery-photo.g2{background:linear-gradient(160deg,#8c5a3a,#d9a877,#b5784c)}
.gallery-photo.g3{background:linear-gradient(160deg,#c9a06a,#ecd3a6,#a87c4e)}
.gallery-photo.g4{background:linear-gradient(160deg,#2e2a28,#6b5848,#1e1b1a)}

/* NEWSLETTER */
.newsletter{height:180px;display:flex;align-items:center;padding:0 80px;gap:30px;border-top:1px solid #e5e5e5}
.newsletter h2{font-size:30px;line-height:1.05}
.newsletter h2 span{display:block;color:var(--green-dark)}
.newsletter-note{width:130px;font-size:11px;color:var(--grey);font-style:italic;border-left:2px solid var(--green);padding-left:12px;line-height:1.5}
.newsletter-input{width:240px;height:40px;border-bottom:1px solid var(--grey-light);color:var(--grey);font-size:13px;padding:10px 4px}
.newsletter .btn{margin-left:auto;display:flex;align-items:center;gap:10px;padding:11px 24px}

/* TESTIMONIALS */
.testimonials{height:440px;background:linear-gradient(180deg,#262626 0%,#1b1b1b 100%);padding-top:50px;color:var(--white);text-align:center}
.testimonials .section-title{color:var(--white)}
.testimonials .section-title h2 span{color:var(--white)}
.testimonials .scissors{color:var(--white)}
.arrow-btn{width:40px;height:40px;border-radius:50%;background:var(--green);display:flex;align-items:center;justify-content:center}
.quote-avatar{width:100px;height:100px;border-radius:50%;margin:36px auto 0;background:radial-gradient(circle at 50% 40%,#e6c8a8,#b48a66);border:4px solid var(--white)}
.quote-text{width:820px;margin:20px auto 0;font-size:12px;color:#cfcfcf;line-height:1.7}
.quote-author{margin-top:14px;font-size:12px}
.quote-author b{color:var(--green);font-weight:600}

/* FOOTER */
.footer{height:240px;background:var(--green-dark);display:flex;padding:34px 80px 0;gap:50px;color:var(--white)}
.footer h4{font-size:16px;margin-bottom:14px}
.footer ul{list-style:none;font-size:12px;line-height:1.8}
.footer ul li::before{content:"› "}
.footer-col{width:210px}
.contact-line{display:flex;gap:10px;font-size:12px;margin-bottom:10px;line-height:1.4}
.contact-line svg{flex:none;margin-top:2px}
.blog-item{display:flex;gap:10px;margin-bottom:14px}
.blog-thumb{width:56px;height:48px;background:linear-gradient(135deg,#7a4a30,#d0a070);flex:none}
.blog-item b{display:block;font-size:12px}
.blog-item span{font-size:11px}
.timing{display:flex;justify-content:space-between;font-size:12px;border-bottom:1px solid rgba(255,255,255,.4);padding:4px 0}
.timing b{font-family:"Oswald",sans-serif;font-weight:500}
.footer-brand{display:flex;align-items:center;gap:10px;font-weight:700;font-size:24px;margin-top:22px}
.footer-brand .brand-dot{background:var(--white)}
.bottombar{height:44px;background:var(--dark);display:flex;align-items:center;justify-content:space-between;padding:0 80px;color:#bdbdbd;font-size:11px}
.social{display:flex;gap:8px}
.social span{width:22px;height:22px;border-radius:50%;border:1px solid #888}
</style>
</head>
<body>

<svg class="icon-defs" aria-hidden="true">
  <symbol id="i-scissors" viewBox="0 0 32 32">
    <circle cx="8" cy="24" r="4.5" fill="none" stroke="currentColor" stroke-width="2"/>
    <circle cx="24" cy="24" r="4.5" fill="none" stroke="currentColor" stroke-width="2"/>
    <path d="M11 20 L24 3 M21 20 L8 3" stroke="currentColor" stroke-width="2" fill="none"/>
  </symbol>
  <symbol id="i-check" viewBox="0 0 12 12">
    <path d="M2 6.5l2.5 2.5L10 3.5" fill="none" stroke="#fff" stroke-width="2"/>
  </symbol>
</svg>

<header class="hero">
  <div class="hero-photo" role="img" aria-label="Photo of a woman with long dark curly hair"></div>
  <div class="hero-shade"></div>
  <div class="topbar">
    <div class="brand"><span class="brand-dot"></span>TrimTable</div>
    <nav class="nav">
      <span>Home</span><span>About Us</span><span>Salon</span><span>Search Result</span><span>Hair Dresser</span><span>Contact Us</span>
      <span class="btn btn-green">Log In</span><span class="btn btn-green">Register</span>
    </nav>
  </div>
  <div class="hero-copy">
    <h1>The Greatest Hair<br>Dresser Booking Site</h1>
    <p class="hero-tag">We give you the look that matters</p>
    <p class="hero-lede">Find the best salons near you, compare treatments and<br>book your next appointment in less than a minute.</p>
    <ul class="usp-list">
      <li><span class="usp-check"><svg width="12" height="12"><use href="#i-check"/></svg></span>Book online 24/7, no phone calls</li>
      <li><span class="usp-check"><svg width="12" height="12"><use href="#i-check"/></svg></span>Thousands of real, verified reviews</li>
      <li><span class="usp-check"><svg width="12" height="12"><use href="#i-check"/></svg></span>Free and instant confirmation</li>
    </ul>
    <div class="hero-actions"><span class="btn btn-green">Book Now</span><span class="btn btn-outline">Download App</span></div>
  </div>
</header>

<section class="search">
  <div class="search-title">Zoek &amp; Vind<br>je kapsalon</div>
  <div class="search-form">
    <div class="field">
      <span class="field-icon"><svg width="14" height="16" viewBox="0 0 12 14"><path d="M6 13C2 8 1 6 1 5a5 5 0 0 1 10 0c0 1-1 3-5 8z" fill="#fff"/></svg></span>
      <span class="field-input">Stad of postcode</span>
    </div>
    <div class="field">
      <span class="field-icon"><svg width="16" height="16" style="color:#fff"><use href="#i-scissors"/></svg></span>
      <span class="field-input">Behandeling</span>
    </div>
    <span class="btn search-btn"><svg width="16" height="16" viewBox="0 0 46 46"><circle cx="19" cy="19" r="13" fill="none" stroke="#fff" stroke-width="5"/><path d="M29 29l12 12" stroke="#fff" stroke-width="6"/></svg>Zoeken</span>
  </div>
</section>

<section class="services">
  <div class="section-title services-title">
    <span class="rule"></span><h2>Our Services</h2><svg class="scissors"><use href="#i-scissors"/></svg><span class="rule"></span>
  </div>
  <div class="service-list">
    <div class="service">
      <div class="service-icon"><svg width="34" height="34"><use href="#i-scissors"/></svg></div>
      <h3>Cutting and Styling</h3><p>Precise cuts and modern styles shaped to suit your face and daily routine.</p>
    </div>
    <div class="service">
      <div class="service-icon"><svg width="34" height="34" viewBox="0 0 32 32"><rect x="13" y="14" width="6" height="16" rx="2" fill="#2b2b2b"/><path d="M10 14h12l-2-12h-8z" fill="none" stroke="#2b2b2b" stroke-width="2"/></svg></div>
      <h3>Hair Color</h3><p>Soft highlights, bold tones and full colour done with gentle products.</p>
    </div>
    <div class="service">
      <div class="service-icon"><svg width="34" height="34" viewBox="0 0 32 32"><rect x="9" y="10" width="14" height="20" rx="3" fill="none" stroke="#2b2b2b" stroke-width="2"/><rect x="12" y="3" width="8" height="7" fill="#2b2b2b"/></svg></div>
      <h3>Hair Treatment</h3><p>Deep care masks and repair rituals that bring back shine and strength.</p>
    </div>
    <div class="service">
      <div class="service-icon"><svg width="34" height="34" viewBox="0 0 32 32"><circle cx="16" cy="16" r="12" fill="none" stroke="#2b2b2b" stroke-width="2"/><path d="M8 18q8 12 16 0" fill="#2b2b2b"/></svg></div>
      <h3>Beard Treatment</h3><p>Clean trims, sharp lines and hot towel shaves for a well groomed look.</p>
    </div>
    <div class="service">
      <div class="service-icon"><svg width="34" height="34" viewBox="0 0 32 32"><path d="M16 3l3.6 8.2 8.9.8-6.7 5.9 2 8.7L16 22l-7.8 4.6 2-8.7-6.7-5.9 8.9-.8z" fill="none" stroke="#2b2b2b" stroke-width="2"/></svg></div>
      <h3>The Finish</h3><p>Blow dry, styling and the final touches that make every look complete.</p>
    </div>
  </div>
</section>

<section class="welcome">
  <div class="welcome-photo" role="img" aria-label="Two photos of women with styled hair"></div>
  <div class="welcome-copy">
    <div class="welcome-head">
      <svg class="pin-badge" viewBox="0 0 40 48"><path d="M20 47C8 32 2 24 2 17a18 18 0 0 1 36 0c0 7-6 15-18 30z" fill="var(--green)"/><circle cx="20" cy="17" r="7" fill="#fff"/></svg>
      <h2>Welcome To<span>TrimTable</span></h2>
      <span class="rule"></span>
      <svg class="scissors"><use href="#i-scissors"/></svg>
    </div>
    <p>TrimTable brings every salon in the country together in one calm place. Browse real reviews, see open time slots and choose the stylist who fits you best, all without making a single phone call. Your next visit to the hairdresser should feel like a treat, and that starts with booking it.</p>
    <p>From a quick trim to a full colour session, you see prices and durations up front. Salons manage their agenda with ease, while you receive a clear confirmation and a friendly reminder before the day arrives.</p>
    <span class="btn btn-green">Get Started</span>
  </div>
</section>

<section class="stats" aria-label="Platform figures">
  <div class="stat">
    <svg class="stat-ring" viewBox="0 0 120 150"><circle cx="60" cy="60" r="56" fill="none" stroke="#fff" stroke-width="2"/><path d="M50 116 L60 140 L70 116" fill="none" stroke="#fff" stroke-width="2"/><text x="60" y="70" text-anchor="middle" fill="#fff" font-family="Oswald" font-size="28">542</text></svg>
    <h3>Grooming</h3>
  </div>
  <div class="stat">
    <svg class="stat-ring" viewBox="0 0 120 150"><circle cx="60" cy="60" r="56" fill="none" stroke="#fff" stroke-width="2"/><path d="M50 116 L60 140 L70 116" fill="none" stroke="#fff" stroke-width="2"/><text x="60" y="70" text-anchor="middle" fill="#fff" font-family="Oswald" font-size="28">16.375</text></svg>
    <h3>Booking For<br>Treatments</h3>
  </div>
  <div class="stat">
    <svg class="stat-ring" viewBox="0 0 120 150"><circle cx="60" cy="60" r="56" fill="none" stroke="#fff" stroke-width="2"/><path d="M50 116 L60 140 L70 116" fill="none" stroke="#fff" stroke-width="2"/><text x="60" y="70" text-anchor="middle" fill="#fff" font-family="Oswald" font-size="28">571.596</text></svg>
    <h3>Agreements</h3>
  </div>
  <div class="stat">
    <svg class="stat-ring" viewBox="0 0 120 150"><circle cx="60" cy="60" r="56" fill="none" stroke="#fff" stroke-width="2"/><path d="M50 116 L60 140 L70 116" fill="none" stroke="#fff" stroke-width="2"/><text x="60" y="70" text-anchor="middle" fill="#fff" font-family="Oswald" font-size="28">7.171</text></svg>
    <h3>Hairdressers<br>Booking</h3>
  </div>
  <div class="stat">
    <svg class="stat-ring" viewBox="0 0 120 150"><circle cx="60" cy="60" r="56" fill="none" stroke="#fff" stroke-width="2"/><path d="M50 116 L60 140 L70 116" fill="none" stroke="#fff" stroke-width="2"/><text x="60" y="70" text-anchor="middle" fill="#fff" font-family="Oswald" font-size="28">26.625</text></svg>
    <h3>Reliable<br>Reviews</h3>
  </div>
</section>

<section class="app">
  <div class="app-copy">
    <h2>All The Hairdressers Of Netherlands In Your Pocket ?</h2>
    <p>Download the app to book on the go, keep your favourite salons close and<br>rebook your usual treatment with a single tap, wherever you are.<br>Simple, fast and always in your pocket.</p>
    <span class="btn btn-green">Download The App</span>
  </div>
  <div class="app-device" role="img" aria-label="Smartphone showing the booking app screen"></div>
</section>

<section class="how">
  <div class="section-title">
    <svg class="scissors"><use href="#i-scissors"/></svg><span class="rule"></span>
    <h2>How Does<span>It Works</span></h2>
    <span class="rule"></span><svg class="scissors"><use href="#i-scissors"/></svg>
  </div>
  <div class="how-steps">
    <svg class="how-path" viewBox="0 0 1200 300" aria-hidden="true">
      <path d="M130 102 C330 -10 420 -10 600 102 S 870 214 1070 102" fill="none" stroke="var(--green)" stroke-width="2" stroke-dasharray="6 6"/>
      <path d="M1050 92 L1072 102 L1056 118" fill="none" stroke="var(--green)" stroke-width="2"/>
    </svg>
    <div class="step" style="left:0">
      <div class="step-icon"><svg width="46" height="46" viewBox="0 0 46 46"><circle cx="19" cy="19" r="13" fill="none" stroke="#2b2b2b" stroke-width="3"/><path d="M29 29l12 12" stroke="#2b2b2b" stroke-width="4"/></svg></div>
      <h3>Search &amp; Find<br>Hairdresser</h3>
    </div>
    <div class="step" style="left:470px">
      <div class="step-icon"><svg width="46" height="46" viewBox="0 0 46 46"><rect x="5" y="8" width="36" height="32" fill="none" stroke="#2b2b2b" stroke-width="3"/><path d="M5 16h36M13 4v8M33 4v8" stroke="#2b2b2b" stroke-width="3"/><path d="M15 28l6 6 11-11" fill="none" stroke="var(--green-dark)" stroke-width="3"/></svg></div>
      <h3>Book Your Appointment<br>Online With 100 % Certainty</h3>
    </div>
    <div class="step" style="left:940px">
      <div class="step-icon"><svg width="46" height="46" viewBox="0 0 32 32"><path d="M16 3l3.6 8.2 8.9.8-6.7 5.9 2 8.7L16 22l-7.8 4.6 2-8.7-6.7-5.9 8.9-.8z" fill="none" stroke="#2b2b2b" stroke-width="2"/></svg></div>
      <h3>Enjoy Your New<br>Hairstyle</h3>
    </div>
  </div>
</section>

<section class="portfolio">
  <div class="section-title">
    <svg class="scissors"><use href="#i-scissors"/></svg><span class="rule"></span>
    <h2>Proud<span>Portfolio</span></h2>
    <span class="rule"></span><svg class="scissors"><use href="#i-scissors"/></svg>
  </div>
  <p class="portfolio-intro">A selection of looks created by salons on our platform. Fresh cuts, warm colours and soft curls made by talented stylists who<br>care about every detail, so you can find inspiration before you book your own appointment.</p>
  <div class="gallery">
    <div class="gallery-lead">
      <h3>From Gallery</h3>
      <p>Browse recent work from stylists near you and save the looks you love for your next visit.</p>
      <div class="gallery-arrows">
        <span><svg width="10" height="10" viewBox="0 0 10 10"><path d="M7 1L3 5l4 4" stroke="#fff" stroke-width="2" fill="none"/></svg></span>
        <span><svg width="10" height="10" viewBox="0 0 10 10"><path d="M3 1l4 4-4 4" stroke="#fff" stroke-width="2" fill="none"/></svg></span>
      </div>
    </div>
    <div class="gallery-photo g1" role="img" aria-label="Woman with long curly hair"></div>
    <div class="gallery-photo g2" role="img" aria-label="Woman with copper waves"></div>
    <div class="gallery-photo g3" role="img" aria-label="Woman with blonde styled hair"></div>
    <div class="gallery-photo g4" role="img" aria-label="Man with short modern haircut"></div>
  </div>
</section>

<section class="newsletter">
  <h2>Newsletter<span>Signup</span></h2>
  <p class="newsletter-note">Style tips and salon deals in your inbox.</p>
  <span class="newsletter-input">Your Name</span>
  <span class="newsletter-input">Your Email</span>
  <span class="btn btn-green"><svg width="18" height="16" viewBox="0 0 18 16"><path d="M1 8L17 1l-4 14-4-5z" fill="#fff"/></svg>Subscribe</span>
</section>

<section class="testimonials">
  <div class="section-title">
    <span class="arrow-btn"><svg width="12" height="12" viewBox="0 0 10 10"><path d="M7 1L3 5l4 4" stroke="#fff" stroke-width="2" fill="none"/></svg></span>
    <span class="rule"></span><svg class="scissors"><use href="#i-scissors"/></svg>
    <h2>What Our<span>Customers Say</span></h2>
    <svg class="scissors"><use href="#i-scissors"/></svg><span class="rule"></span>
    <span class="arrow-btn"><svg width="12" height="12" viewBox="0 0 10 10"><path d="M3 1l4 4-4 4" stroke="#fff" stroke-width="2" fill="none"/></svg></span>
  </div>
  <div class="quote-avatar" role="img" aria-label="Customer portrait"></div>
  <p class="quote-text">I found a lovely salon just around the corner and booked a colour appointment in under a minute. The reminder arrived on time, the price was exactly as shown and my stylist already knew what I wanted. Booking my hairdresser has never felt this relaxed, and I will use it again for every visit.</p>
  <p class="quote-author"><b>Mira Olsen</b> | CUSTOMER</p>
</section>

<footer class="footer">
  <div class="footer-col" style="width:160px">
    <h4>Quick Links</h4>
    <ul><li>Home</li><li>About Us</li><li>Salon</li><li>Search</li><li>Blog</li><li>Contact Us</li></ul>
  </div>
  <div class="footer-col">
    <h4>Contact Details</h4>
    <div class="contact-line"><svg width="12" height="14" viewBox="0 0 12 14"><path d="M6 13C2 8 1 6 1 5a5 5 0 0 1 10 0c0 1-1 3-5 8z" fill="#fff"/></svg>Prinsenlaan 48, 1012 AB<br>Amsterdam, Netherlands</div>
    <div class="contact-line"><svg width="12" height="12" viewBox="0 0 12 12"><path d="M2 1h3l1 3-2 1a7 7 0 0 0 3 3l1-2 3 1v3c-6 0-10-4-10-9z" fill="#fff"/></svg>+31 20 555 0182</div>
    <div class="contact-line"><svg width="14" height="10" viewBox="0 0 14 10"><rect x="0.5" y="0.5" width="13" height="9" fill="none" stroke="#fff"/><path d="M1 1l6 5 6-5" fill="none" stroke="#fff"/></svg>hello@trimtable.com</div>
  </div>
  <div class="footer-col" style="width:240px">
    <h4>Latest Blog</h4>
    <div class="blog-item"><div class="blog-thumb" role="img" aria-label="Blog photo of a hairstyle"></div><div><b>Summer Hair Trends</b><span>12 June 2015</span></div></div>
    <div class="blog-item"><div class="blog-thumb" role="img" aria-label="Blog photo of a salon"></div><div><b>Caring For Curls</b><span>28 May 2015</span></div></div>
  </div>
  <div class="footer-col" style="width:230px;margin-left:auto">
    <h4>Office Timings</h4>
    <div class="timing"><b>MON - FRI</b><span>9:00 AM - 7:00 PM</span></div>
    <div class="timing"><b>SAT</b><span>9:00 AM - 5:00 PM</span></div>
    <div class="timing"><b>SUN</b><span>CLOSED</span></div>
    <div class="footer-brand"><span class="brand-dot"></span>TrimTable</div>
  </div>
</footer>
<div class="bottombar">
  <span>Copyright 2015 TrimTable &nbsp;|&nbsp; All Rights Reserved</span>
  <div class="social"><span></span><span></span><span></span><span></span></div>
</div>

</body>
</html>
```